High profile consulting company needs a Business Card Design

I need a business card design for a coaching /consulting company. We specialize in changing behaviors. Our services include therapy, workshops, life coaching, etc.

Check out our website to get a feel for our personality. www.oakbridgeadvisory.com

The new logo will be attached to the website soon, I have attached the new logo for your use on the business card.
Updates

I forgot to provide you with the company email under the "must have" section for the business card.  The website is:

 www.oakbridgeadvisory.com

I understand there's some trouble with the logo I uploaded.  I will try that again.  Thank you for your efforts.

Dana

Thank you for some of your questions.  I prefer a one sided business card, and tend to like the white backgrounds.

I also made 2 small changes to the content.  

add MFT after the name:  Dana Holloway, MFT

and the tag line needed more clarity once I saw it.  Please change it to:  Building stronger teams through trusted relationships and lasting growth.

Thank you,
Dana

Industry/Entity Type

Business

Requirements
Must have
• logo
Phone number: 415-207-5146
email: Dana@oakbridgeadvisory.com
Dana Holloway, MFT
President
Nice to have
• Building stronger teams through trusted relationships and lasting growth.

```html
<!DOCTYPE html>
<html lang="en">
<head>
<meta charset="UTF-8">
<title>Oakbridge Advisory — Business Card</title>
<link rel="stylesheet" href="https://fonts.googleapis.com/css2?family=Montserrat:wght@600&family=Arimo:ital,wght@0,400;1,400&family=Tinos:wght@400&display=swap">
<style>
  :root {
    --backdrop: #8c8c8c;
    --card-white: #ffffff;
    --brand-green: #14785a;
    --brand-green-dark: #0f6049;
    --rule-grey: #b8bcbd;
    --ink-white: #ffffff;
  }
  * { box-sizing: border-box; margin: 0; padding: 0; }
  html, body {
    width: 1200px; height: 951px; overflow: hidden;
    background: var(--backdrop);
  }
  .stage { position: relative; width: 1200px; height: 951px; }

  .card {
    position: absolute;
    width: 560px; height: 320px;
    background: var(--card-white);
    border-radius: 18px;
    overflow: hidden;
  }
  .card--front { left: 70px; top: 80px; }
  .card--back  { left: 570px; top: 540px; }

  /* Brand lockup: plain circle + name in one colour, one weight */
  .brand { position: absolute; display: flex; align-items: center; gap: 16px; }
  .brand__dot {
    width: 74px; height: 74px; border-radius: 50%;
    background: var(--brand-green); flex: none;
  }
  .brand__name {
    font-family: "Montserrat", sans-serif; font-weight: 600;
    color: var(--brand-green); line-height: 1.05;
  }
  .brand__line1 { display: block; font-size: 38px; letter-spacing: 1px; }
  .brand__line2 { display: block; font-size: 24px; letter-spacing: 9px; }

  .card--front .brand { left: 48px; top: 118px; }

  .card--back .brand { left: 72px; top: 26px; }
  .card--back .brand__dot { width: 66px; height: 66px; }
  .card--back .brand__line1 { font-size: 34px; }
  .card--back .brand__line2 { font-size: 21px; letter-spacing: 8px; }

  .tagline {
    position: absolute; left: 0; right: 0; top: 116px;
    text-align: center;
    font-family: "Arimo", sans-serif; font-size: 10.5px;
    font-style: italic; text-transform: uppercase;
    color: var(--brand-green); letter-spacing: 0.2px;
    white-space: nowrap;
  }
  .back__rule {
    position: absolute; left: 0; right: 0; top: 134px; height: 4px;
    background: var(--rule-grey);
  }
  .back__band {
    position: absolute; left: 0; right: 0; top: 138px; bottom: 0;
    background: linear-gradient(180deg, var(--brand-green) 0%, var(--brand-green-dark) 100%);
    color: var(--ink-white); text-align: center;
  }
  .person {
    margin-top: 20px;
    font-family: "Tinos", serif; font-size: 26px;
  }
  .person__cred { font-size: 16px; }
  .role {
    font-family: "Arimo", sans-serif; font-size: 15px; margin-top: 2px;
  }
  .contact {
    margin-top: 20px;
    font-family: "Arimo", sans-serif; font-size: 18px; line-height: 1.25;
    list-style: none;
  }
</style>
</head>
<body>
<main class="stage">

  <section class="card card--front" aria-label="Business card front">
    <div class="brand">
      <span class="brand__dot" aria-hidden="true"></span>
      <span class="brand__name">
        <span class="brand__line1">OAKBRIDGE</span>
        <span class="brand__line2">ADVISORY</span>
      </span>
    </div>
  </section>

  <section class="card card--back" aria-label="Business card back">
    <div class="brand">
      <span class="brand__dot" aria-hidden="true"></span>
      <span class="brand__name">
        <span class="brand__line1">OAKBRIDGE</span>
        <span class="brand__line2">ADVISORY</span>
      </span>
    </div>
    <p class="tagline">Building stronger teams through trusted relationships and lasting growth</p>
    <div class="back__rule" aria-hidden="true"></div>
    <div class="back__band">
      <p class="person">Dana Holloway, <span class="person__cred">MFT</span></p>
      <p class="role">President</p>
      <ul class="contact">
        <li>415-207-5146</li>
        <li>Dana@oakbridgeadvisory.com</li>
        <li>www.oakbridgeadvisory.com</li>
      </ul>
    </div>
  </section>

</main>
</body>
</html>
```